We need a flyer designed for our 4th Annual Harvestlight: A Kinfolk Homecoming for the Heritage Festival that includes the day, time, location, address, and logos. It also needs to include what to expect. The event will be held on Saturday June 14th from 12p-6p at Cedar Commons located at 417 N. Bellmora St., Pensacola, FL 32507. Please see uploaded files for prior flyers for reference when it comes to information to include. Also I've uploaded pictures from our prior festivals that you may incorporate and logos.

```html
<!DOCTYPE html>
<html lang="en">
<head>
<meta charset="utf-8">
<title>4th Annual Harvestlight – A Kinfolk Homecoming for the Heritage Festival</title>
<link rel="stylesheet" href="https://fonts.googleapis.com/css2?family=Anton&family=Open+Sans:wght@400;700;800&family=PT+Sans:wght@400;700&display=swap">
<style>
  :root {
    --ink: #000000;
    --white: #ffffff;
    --sun: #ffe600;
    --amber: #f7a81b;
    --orange: #f08a24;
    --red: #e8262b;
    --magenta: #d81b7a;
    --violet: #5b2b86;
    --blue: #1c8fd1;
    --green: #2fa84f;
    --lime: #c6d92e;
    --pill: #b5b5b5;
    --plate: #141414;
    --gold: #c9952b;
  }
  * { box-sizing: border-box; margin: 0; padding: 0; }
  html, body { width: 927px; height: 1200px; overflow: hidden; background: var(--ink); }
  .flyer {
    position: relative; width: 927px; height: 1200px; overflow: hidden;
    font-family: "Open Sans", sans-serif; color: var(--ink); background: var(--ink);
  }
  .rays {
    position: absolute; inset: 0 0 auto 0; height: 930px;
    background:
      linear-gradient(200deg, rgba(255,230,0,0.85) 0%, rgba(255,230,0,0) 45%),
      conic-gradient(from 200deg at 62% 62%,
        var(--sun) 0deg, var(--amber) 30deg, var(--red) 60deg, var(--magenta) 95deg,
        var(--violet) 130deg, var(--blue) 165deg, var(--green) 200deg, var(--lime) 235deg,
        var(--sun) 270deg, var(--orange) 310deg, var(--sun) 360deg);
  }
  .crowd {
    position: absolute; left: 0; right: 0; top: 690px; height: 250px;
    background: linear-gradient(180deg, rgba(0,0,0,0) 0%, rgba(0,0,0,0.85) 45%, var(--ink) 85%);
  }
  .tagline {
    position: absolute; left: 422px; top: 140px;
    font-size: 27px; font-weight: 400; letter-spacing: 0.2px; white-space: nowrap;
  }
  .host {
    position: absolute; left: 365px; top: 196px; width: 482px;
    font-size: 33px; font-weight: 800; line-height: 1.15; text-align: center; color: var(--ink);
  }
  .presents {
    position: absolute; left: 0; width: 1186px; top: 286px; text-align: center;
    font-size: 30px; font-weight: 800;
  }
  .banner-photo {
    position: absolute; left: 30px; top: 368px; width: 856px; height: 198px; border-radius: 60px 60px 24px 24px;
    background:
      radial-gradient(ellipse at 20% 30%, rgba(232,38,43,0.9), rgba(232,38,43,0) 40%),
      radial-gradient(ellipse at 50% 20%, rgba(47,168,79,0.9), rgba(47,168,79,0) 40%),
      radial-gradient(ellipse at 80% 30%, rgba(255,230,0,0.9), rgba(255,230,0,0) 40%),
      linear-gradient(180deg, #3a7a3a 0%, #d8d8d8 60%, #bdbdbd 100%);
    opacity: 0.85;
  }
  .edition {
    position: absolute; left: 389px; top: 412px; font-size: 38px; font-weight: 800; white-space: nowrap;
  }
  .edition sup { font-size: 22px; vertical-align: 16px; }
  .title {
    position: absolute; left: 0; right: 0; top: 452px; text-align: center;
    font-family: "Anton", sans-serif; font-size: 104px; line-height: 1; letter-spacing: 3px;
    color: var(--white); text-shadow: 0 4px 6px rgba(0,0,0,0.45);
  }
  .subtitle {
    position: absolute; left: 0; right: 0; top: 580px; text-align: center;
    font-size: 28px; font-weight: 700; white-space: nowrap;
  }
  .features {
    position: absolute; left: 20px; right: 20px; top: 946px; text-align: center;
    font-family: "PT Sans", sans-serif; font-size: 21px; line-height: 26px; color: var(--orange);
  }
  .when {
    position: absolute; left: 60px; top: 1022px; width: 240px; text-align: center; color: var(--white);
  }
  .when .day { font-size: 29px; font-weight: 800; line-height: 1; }
  .when .date { font-family: "Anton", sans-serif; font-size: 62px; line-height: 1; color: var(--sun); }
  .when .date sup { font-size: 32px; vertical-align: 24px; }
  .when .time { font-size: 21px; font-weight: 800; line-height: 1.1; }
  .where {
    position: absolute; left: 326px; top: 1031px; width: 303px; height: 91px; border-radius: 46px;
    background: var(--pill); display: flex; align-items: center; padding-left: 20px; gap: 12px;
  }
  .where svg { width: 36px; height: 54px; flex: none; }
  .where .venue { font-size: 25px; font-weight: 800; line-height: 1.05; }
  .where .address { font-size: 16px; font-weight: 700; line-height: 1.3; }
  .sponsor {
    position: absolute; left: 660px; top: 1049px; width: 237px; height: 55px; background: var(--plate);
    display: flex; align-items: center; gap: 10px; padding-left: 12px;
  }
  .sponsor .mark { width: 26px; height: 26px; background: var(--gold); flex: none; }
  .sponsor .name { font-size: 15px; font-weight: 700; color: var(--white); white-space: nowrap; }
</style>
</head>
<body>
<main class="flyer">
  <div class="rays" role="img" aria-label="Bright multicolour burst of rays with paint splatters"></div>
  <div class="crowd" role="img" aria-label="Silhouettes of a cheering festival crowd with raised arms"></div>

  <p class="tagline">CUMMUNITY | ARTS | CULTURE</p>
  <p class="host">The Hollis Family Foundation</p>
  <p class="presents">PRESENTS</p>

  <div class="banner-photo" role="img" aria-label="Photo of a large lit marquee sign framed by red, yellow, green and black balloon arches"></div>
  <p class="edition">4<sup>th</sup> Annual</p>
  <h1 class="title">HARVESTLIGHT</h1>
  <p class="subtitle">A Kinfolk Homecoming for the Heritage Festival</p>

  <p class="features">LIVE PERFORMANCES | FOOD VENDORS | ART/AFRICAN CLOTHING | KIDS OBSTACLE COURSE &amp;<br>PLAY AREA | SPADES &amp; DOMINO TABLES | BRING YOUR OWN CHAIRS OR PICNIC BLANKETS</p>

  <div class="when">
    <p class="day">SATURDAY</p>
    <p class="date">June 14<sup>th</sup></p>
    <p class="time">12PM-6PM</p>
  </div>

  <div class="where">
    <svg viewBox="0 0 36 54" aria-hidden="true"><path d="M18 2C9 2 2 9 2 18c0 12 16 34 16 34s16-22 16-34C34 9 27 2 18 2zm0 23a7 7 0 1 1 0-14 7 7 0 0 1 0 14z" fill="#000"/></svg>
    <div>
      <p class="venue">CEDAR COMMONS</p>
      <p class="address">417 N. Bellmora St.,<br>Pensacola, FL 32507.</p>
    </div>
  </div>

  <div class="sponsor">
    <span class="mark"></span>
    <span class="name">The Brantley Firm, PLLC</span>
  </div>
</main>
</body>
</html>
```